Luxury Business Card Design for High-End Window Treatments

Gilded Slatworks
Custom Plantation Shutters & Architectural Shading Systems

⸻

BACK

Daniel Trevick
Owner

Custom Interior & Exterior Window Treatments

919-555-0148
gildedslatworks.com

I have included a picture that I’m hoping we can use on the back, but I’m also wondering if you can get rid of the ladder? Should we get rid of shutters , shades and blinds underneath Gilded Slatworks?

Target Market(s)

High-end residential homeowners, custom home builders, architects, interior designers, and luxury renovation clients seeking premium plantation shutters and motorized architectural shading systems.

Industry/Entity Type

Custom Window treatments

Contact Information for Business Card

Front Gilded Slatworks Custom Plantation Shutters Motorized Architectural Shading Systems BACK Daniel Trevick Owner 919-555-0148 GildedSlatworks.com Custom Interior & Exterior Window Treatments By Appointment

Requirements
Nice to have
• Not 100% sure on nice to halves or the color but you can definitely check out my website to get a better understanding of what I’m trying to do

```html
<!DOCTYPE html>
<html lang="en">
<head>
<meta charset="UTF-8">
<title>Gilded Slatworks — Business Card Front</title>
<link rel="stylesheet" href="https://fonts.googleapis.com/css2?family=Tinos&family=Belleza&display=swap">
<style>
  :root {
    --card-slate: #343a42;
    --name-ivory: #ecebe4;
    --accent-gold: #f5d466;
  }
  html, body {
    margin: 0;
    padding: 0;
    width: 1200px;
    height: 686px;
    overflow: hidden;
    background: var(--card-slate);
  }
  .card-front {
    position: relative;
    width: 1200px;
    height: 686px;
    background: var(--card-slate);
  }
  .brand-name {
    position: absolute;
    left: 0;
    right: 0;
    top: 196px;
    margin: 0;
    text-align: center;
    font-family: "Tinos", serif;
    font-weight: 400;
    font-size: 84px;
    line-height: 88px;
    color: var(--name-ivory);
    letter-spacing: 1px;
  }
  .brand-name span {
    display: block;
  }
  .product-line {
    position: absolute;
    left: 418px;
    width: 366px;
    top: 382px;
    margin: 0;
    display: flex;
    justify-content: space-between;
    font-family: "Belleza", sans-serif;
    font-size: 36px;
    line-height: 40px;
    color: var(--accent-gold);
  }
  .service-tagline {
    position: absolute;
    left: 0;
    right: 0;
    top: 512px;
    margin: 0;
    text-align: center;
    font-family: "Tinos", serif;
    font-size: 29px;
    line-height: 34px;
    letter-spacing: 2.4px;
    color: var(--accent-gold);
  }
</style>
</head>
<body>
  <main class="card-front">
    <h1 class="brand-name"><span>Gilded</span><span>Slatworks</span></h1>
    <p class="product-line"><span>Shutters</span><span>Shades</span><span>Blinds</span></p>
    <p class="service-tagline">Custom Plantation Shutters &amp; Architectural Shading Systems</p>
  </main>
</body>
</html>
```